holloway paving service

Needs to have phone number 0418259730 and email markholloway@brightmail.com.au.
ABN 62318470915
name mark holloway

For all your concreting solutions
Excavation
Exposed & colour concrete
House & shed slabs
Driveways
Landing & steps

Contact Information for Business Card

ph 0418259730
email markholloway@brightmail.com.au.
ABN 62318470915
name mark holloway

```html
<!DOCTYPE html>
<html lang="en">
<head>
<meta charset="utf-8">
<title>Holloway Paving Service – Business Card</title>
<link rel="stylesheet" href="https://fonts.googleapis.com/css2?family=Montserrat:wght@400;500;600;700&display=swap">
<style>
  :root {
    --canvas-bg: #e9e7e3;
    --card-white: #ffffff;
    --brand-orange: #ec6a24;
    --chevron-grey: #ebebeb;
    --rule-grey: #6f6f6f;
    --text-grey: #6a6a6a;
    --text-white: #ffffff;
  }
  * { box-sizing: border-box; margin: 0; padding: 0; }
  html, body { width: 1200px; height: 886px; overflow: hidden; }
  body {
    background: var(--canvas-bg);
    font-family: "Montserrat", sans-serif;
    position: relative;
  }
  .card {
    position: absolute;
    top: 145px;
    width: 340px;
    height: 595px;
    background: var(--card-white);
    box-shadow: 0 6px 18px rgba(0,0,0,0.12);
    overflow: hidden;
  }
  .card--front { left: 220px; }
  .card--back { left: 640px; }

  .front-shapes { position: absolute; inset: 0; }

  .front-header {
    position: absolute;
    top: 42px; left: 0; right: 0;
    text-align: center;
    color: var(--brand-orange);
  }
  .business-name {
    font-weight: 600;
    font-size: 21px;
    letter-spacing: 0.5px;
    line-height: 1.1;
    text-transform: uppercase;
  }
  .business-name__sub {
    display: flex;
    align-items: center;
    justify-content: center;
    gap: 10px;
  }
  .business-name__sub::before,
  .business-name__sub::after {
    content: "";
    width: 58px;
    height: 2px;
    background: var(--rule-grey);
  }
  .phone {
    font-weight: 500;
    font-size: 15px;
    letter-spacing: 2px;
    margin-top: 2px;
  }

  .contact {
    position: absolute;
    left: 0; right: 0;
    top: 430px;
    text-align: center;
    color: var(--text-white);
  }
  .contact__name {
    font-weight: 700;
    font-size: 22px;
    letter-spacing: 1px;
    text-transform: uppercase;
  }
  .contact__line {
    font-weight: 400;
    font-size: 13px;
    margin-top: 6px;
  }

  .back-lockup {
    position: absolute;
    top: 70px; left: 0; right: 0;
    display: flex;
    align-items: center;
    justify-content: center;
    gap: 12px;
  }
  .back-lockup__square {
    width: 34px; height: 34px;
    background: var(--brand-orange);
    flex: none;
  }
  .back-lockup__text { color: var(--brand-orange); text-align: center; }
  .back-lockup .business-name { font-size: 15px; }
  .back-lockup .business-name__sub::before,
  .back-lockup .business-name__sub::after { width: 30px; height: 1.5px; }
  .back-lockup .phone { font-size: 11px; letter-spacing: 1.5px; }

  .services {
    position: absolute;
    top: 315px; left: 0; right: 0;
    list-style: none;
    text-align: center;
    color: var(--text-grey);
    font-size: 14px;
    line-height: 1.55;
  }
</style>
</head>
<body>
  <section class="card card--front" aria-label="Business card front">
    <svg class="front-shapes" width="340" height="595" viewBox="0 0 340 595" aria-hidden="true">
      <polygon points="0,150 340,150 340,205 170,340 0,205" fill="var(--chevron-grey)"/>
      <polygon points="0,218 170,353 340,218 340,595 0,595" fill="var(--brand-orange)"/>
      <polyline points="0,205 170,340 340,205" fill="none" stroke="var(--rule-grey)" stroke-width="5"/>
    </svg>
    <header class="front-header">
      <p class="business-name">Holloway Paving</p>
      <p class="business-name business-name__sub">Service</p>
      <p class="phone">0418259730</p>
    </header>
    <div class="contact">
      <p class="contact__name">Mark Holloway</p>
      <p class="contact__line">markholloway@brightmail.com.au</p>
      <p class="contact__line">ABN 62318470915</p>
    </div>
  </section>

  <section class="card card--back" aria-label="Business card back">
    <div class="back-lockup">
      <span class="back-lockup__square" aria-hidden="true"></span>
      <div class="back-lockup__text">
        <p class="business-name">Holloway Paving</p>
        <p class="business-name business-name__sub">Service</p>
        <p class="phone">0418259730</p>
      </div>
    </div>
    <ul class="services">
      <li>Excavation</li>
      <li>Exposed &amp; colour concrete</li>
      <li>House &amp; shed slabs</li>
      <li>Driveways</li>
      <li>Landing &amp; steps</li>
    </ul>
  </section>
</body>
</html>
```